holloway paving service

Needs to have phone number 0418259730 and email markholloway@brightmail.com.au.
ABN 62318470915
name mark holloway

For all your concreting solutions
Excavation
Exposed & colour concrete
House & shed slabs
Driveways
Landing & steps

Contact Information for Business Card

ph 0418259730
email markholloway@brightmail.com.au.
ABN 62318470915
name mark holloway

```html
<!DOCTYPE html>
<html lang="en">
<head>
<meta charset="utf-8">
<title>Holloway Paving Service – Business Card</title>
<link href="https://fonts.googleapis.com/css2?family=Roboto:wght@400;500;700&family=Roboto+Condensed:wght@700&display=swap" rel="stylesheet">
<style>
  :root {
    --backdrop: #2e2e2e;
    --card-white: #f3f3f3;
    --brand-orange: #f26a24;
    --brand-grey: #5d5d5d;
    --text-white: #ffffff;
  }
  html, body {
    margin: 0;
    padding: 0;
    width: 1200px;
    height: 960px;
    overflow: hidden;
    background: var(--backdrop);
    font-family: "Roboto", Arial, sans-serif;
  }
  .canvas {
    position: relative;
    width: 1200px;
    height: 960px;
  }
  .card {
    position: absolute;
    width: 600px;
    height: 343px;
    overflow: hidden;
    box-shadow: 0 3px 8px rgba(0,0,0,0.45);
  }
  .card-front {
    left: 321px;
    top: 110px;
    background: var(--card-white);
  }
  .card-back {
    left: 320px;
    top: 493px;
    background: var(--brand-orange);
  }
  .front-shapes {
    position: absolute;
    inset: 0;
  }
  .brand-lockup {
    position: absolute;
    right: 30px;
    top: 44px;
    display: flex;
    align-items: center;
    gap: 12px;
  }
  .brand-mark {
    width: 42px;
    height: 42px;
    background: var(--brand-orange);
  }
  .brand-text {
    display: flex;
    flex-direction: column;
    align-items: center;
    border-left: 2px solid var(--brand-orange);
    padding-left: 10px;
  }
  .brand-name {
    color: var(--brand-orange);
    font-weight: 700;
    font-size: 13px;
    letter-spacing: 0.3px;
    text-transform: uppercase;
    white-space: nowrap;
  }
  .brand-phone {
    color: var(--brand-orange);
    font-weight: 500;
    font-size: 11px;
    letter-spacing: 1.5px;
    margin-top: 3px;
  }
  .contact-block {
    position: absolute;
    left: 27px;
    top: 234px;
    color: var(--text-white);
  }
  .contact-name {
    font-family: "Roboto Condensed", "Arial Narrow", sans-serif;
    font-weight: 700;
    font-size: 22px;
    text-transform: uppercase;
    margin: 0 0 10px;
  }
  .contact-line {
    font-size: 13.5px;
    line-height: 19px;
    margin: 0;
    white-space: nowrap;
  }
  .back-name {
    position: absolute;
    left: 0;
    right: 0;
    top: 140px;
    text-align: center;
    color: var(--text-white);
    font-weight: 700;
    font-size: 30px;
    text-transform: uppercase;
    letter-spacing: 0.5px;
  }
  .services {
    position: absolute;
    left: 0;
    right: 0;
    top: 270px;
    text-align: center;
    color: var(--text-white);
    font-size: 15px;
    line-height: 18px;
  }
  .services p { margin: 0; }
  .bullet { font-size: 9px; vertical-align: 2px; padding: 0 3px; }
</style>
</head>
<body>
<main class="canvas">
  <section class="card card-front" aria-label="Card front">
    <svg class="front-shapes" width="600" height="343" viewBox="0 0 600 343" aria-hidden="true">
      <rect x="380" y="329" width="220" height="14" fill="var(--brand-grey)"/>
      <polygon points="0,215 292,215 395,343 0,343" fill="var(--brand-orange)"/>
      <line x1="292" y1="215" x2="395" y2="343" stroke="#ffffff" stroke-width="2"/>
    </svg>

    <div class="brand-lockup">
      <div class="brand-mark"></div>
      <div class="brand-text">
        <span class="brand-name">Holloway Paving Service</span>
        <span class="brand-phone">0418259730</span>
      </div>
    </div>

    <div class="contact-block">
      <h1 class="contact-name">Mark Holloway</h1>
      <p class="contact-line">P. 0418259730</p>
      <p class="contact-line">E. markholloway@brightmail.com.au</p>
      <p class="contact-line">W. www.hollowaypaving.com.au | ABN 62318470915</p>
    </div>
  </section>

  <section class="card card-back" aria-label="Card back">
    <div class="back-name">Holloway Paving Service</div>
    <div class="services">
      <p>Excavation <span class="bullet">◆</span> Exposed &amp; colour concrete</p>
      <p>House &amp; shed slabs <span class="bullet">◆</span> Driveways <span class="bullet">◆</span> Landing &amp; steps</p>
    </div>
  </section>
</main>
</body>
</html>
```